Stationery Set for Velmora Company

I need to create full stationery design for my company; Business Cards, Envelops, Letter Heads, Calendar.
In the letter head and Envelops... only contact information and website links.
Our company is a Service Management company with different domains of innovative services including Technology Service Management, Education Services, Outsourcing Management, Events Management.
I need a modern and innovative design specially for the business card. I some transparent designs and I like it, but don't limit your innovation to what I mentioned. Sky is limit for your innovation.

Target Market(s)

Middle East & Africa

Industry/Entity Type

Business Management

Colors
34a7d8
0355a3
85acd3
86cae7
cee9f5
cfdeed
e4daeb
f3f1f8
ecf7fb

Requirements
Must have
• Name, Title, Email, Mobile
Nice to have
• We have multiple locations in USA, KSA, EGY, so I need ideas about how to include all contact details maybe QR / Barcode or something else.
• Please see our locations and contact information: www.brightvelmora.example
Should not have
• Too much text

```html
<!DOCTYPE html>
<html lang="en">
<head>
<meta charset="utf-8">
<title>Velmora Company – Business Card</title>
<link href="https://fonts.googleapis.com/css2?family=Open+Sans:wght@400;600;700&display=swap" rel="stylesheet">
<style>
  :root{
    --bg:#ecedef;
    --card:#ffffff;
    --ink:#2c2c2c;
    --brand-blue:#3f6fbf;
    --band:#5a86cc;
    --band-light:#e9eef6;
  }
  *{box-sizing:border-box;margin:0;padding:0}
  html,body{width:1200px;height:950px;overflow:hidden}
  body{background:var(--bg);font-family:"Open Sans",sans-serif;color:var(--ink);position:relative}

  .card{position:absolute;left:290px;width:620px;height:354px;background:var(--card);
    box-shadow:0 8px 24px rgba(0,0,0,.18);overflow:hidden}
  .card--front{top:70px}
  .card--back{top:490px}

  .brand{display:flex;align-items:center;gap:10px}
  .brand__mark{width:16px;height:16px;background:var(--brand-blue);flex:none}
  .brand__name{font-weight:700;color:var(--brand-blue);letter-spacing:.3px;white-space:nowrap}

  .card--front .brand{position:absolute;left:0;right:0;top:120px;justify-content:center}
  .card--front .brand__name{font-size:30px}
  .card--front .website{position:absolute;left:0;right:0;top:226px;text-align:center;
    font-size:14px;font-weight:600;letter-spacing:1.5px}

  .card--back .brand{position:absolute;left:36px;top:104px}
  .card--back .brand__name{font-size:22px}

  .contact{position:absolute;left:362px;top:24px;width:245px;font-size:12.5px;line-height:17px}
  .contact__block{margin-bottom:8px}
  .contact__line{display:flex;align-items:center;gap:8px}
  .contact__line svg{width:12px;height:12px;flex:none;fill:var(--brand-blue)}

  .band{position:absolute;left:0;right:0;bottom:0;height:64px;background:var(--band-light)}
  .nameplate{position:absolute;left:0;bottom:34px;width:336px;height:86px;background:var(--band);
    border-radius:0 18px 18px 0;color:#fff;display:flex;flex-direction:column;justify-content:center;
    align-items:flex-end;padding-right:64px}
  .nameplate__name{font-size:19px;font-weight:700;letter-spacing:.5px}
  .nameplate__title{font-size:14px;font-weight:400}
</style>
</head>
<body>
  <section class="card card--front">
    <div class="brand"><span class="brand__mark"></span><span class="brand__name">Velmora Company</span></div>
    <p class="website">www.brightvelmora.example</p>
  </section>

  <section class="card card--back">
    <div class="brand"><span class="brand__mark"></span><span class="brand__name">Velmora Company</span></div>

    <div class="contact">
      <div class="contact__block">
        <p>418 Harbor Crest Way</p>
        <p>4th Floor Lakemont</p>
        <p>CA 90412 US</p>
        <p class="contact__line"><svg viewBox="0 0 24 24"><path d="M6.6 10.8a15 15 0 0 0 6.6 6.6l2.2-2.2c.3-.3.7-.4 1-.2 1.1.4 2.3.6 3.6.6.6 0 1 .4 1 1V20c0 .6-.4 1-1 1A17 17 0 0 1 3 4c0-.6.4-1 1-1h3.5c.6 0 1 .4 1 1 0 1.3.2 2.5.6 3.6.1.3 0 .7-.2 1z"/></svg>+1.555 010 2288</p>
      </div>
      <div class="contact__block">
        <p>Riyadh, Al Noor District,</p>
        <p>Qasr Al Wadi St.</p>
        <p>Palmyra Buildings</p>
        <p>Block 4C 3rd Floor C12, C14</p>
        <p class="contact__line"><svg viewBox="0 0 24 24"><path d="M6.6 10.8a15 15 0 0 0 6.6 6.6l2.2-2.2c.3-.3.7-.4 1-.2 1.1.4 2.3.6 3.6.6.6 0 1 .4 1 1V20c0 .6-.4 1-1 1A17 17 0 0 1 3 4c0-.6.4-1 1-1h3.5c.6 0 1 .4 1 1 0 1.3.2 2.5.6 3.6.1.3 0 .7-.2 1z"/></svg>+966 90000 11 22</p>
      </div>
      <div class="contact__block">
        <p class="contact__line"><svg viewBox="0 0 24 24"><path d="M7 1h10a2 2 0 0 1 2 2v18a2 2 0 0 1-2 2H7a2 2 0 0 1-2-2V3a2 2 0 0 1 2-2zm0 3v14h10V4z"/></svg>+1.555 010 2288</p>
        <p class="contact__line"><svg viewBox="0 0 24 24"><path d="M2 4h20v16H2zm2 2v.5l8 5 8-5V6z"/></svg>info@brightvelmora.example</p>
      </div>
    </div>

    <div class="band"></div>
    <div class="nameplate">
      <p class="nameplate__name">DANIEL REYES</p>
      <p class="nameplate__title">CEO/Founder</p>
    </div>
  </section>
</body>
</html>
```